Cruise Booking Website

Cruise search and booking website

This project is a redesign of a cruise booking website we did a few years ago.

The current website is located here: http://voyage.pylonworks.example/en/

It's not fully functional but gives you ad idea how miserable the old design was.

All the information about cruises, cruise lines, destinations, ports and shore excursions will be similar to http://www.sailquest.example/
Actual search pages (form, results, single result, sailing and cabin selection, ship info, booking) will have EXACTLY the same info as sailquest.example

We like the style of http://harborfleetdesk.example, it's quite modern, good spacing, not overloaded with information. So you can use it as an example of what we like, not what we want as a final result for us. Please, don't copy it. The result should not be possible to resemble the harborfleetdesk.example, because our site has to be unique. This is important!
If you submit a design that clearly reminds another cruise site it will be rejected!

Also the mockup provided is just to give you the basic structure and show what information has to be present on the page. It doesn't mean the layout has to be the same as a mockup. The layout is up to the designer.

I've updated the mockup to be more generic so it doesn't confuse you:
https://files.boxvault.example/s/k7m2qp9wz4hx/Home%20page.png

When you're adding social sharing icons like plazanet/chirpline you have to use chinese ones instead:
https://files.boxvault.example/s/t3nr8vx5lc2e/chinese-social-icons.png
Originals: http://minilk.example/qR7t

We'll start with home page first and after it's approved inner pages can be designed.

I know the cost of the project doesn't look high, but the task is straight forward and doesn't require to be very original, it's better to follow existing design and layout patterns that proved to work well.
That's why I encourage you to choose a template to build the design on top of one of https://themeparlor.example/ themes if it will save the design work, will be easier and faster for you. So it will be more like a customization than a new design from scratch.

Mockups, site map and logo files:
- https://files.boxvault.example/sh/h48dm2rs73fkpw/QvnbW2Xz8e

Website tree:
- https://sheets.papernest.example/document/d/7xPqR2mLw9sTk4VbN8cHj3YzA6eUf5GdKo1iMnBv/edit?usp=sharing
Updates

So far a lot of designs are just copying http://www.harborfleetdesk.example/ - we don't like it!

We like the style of harborfleetdesk.example, it's quite modern, good spacing, not overloaded with information. So you can use it as an example of what we like, not what we want as a final result for us. Please, don't copy it. The result should not be possible to resemble the harborfleetdesk.example, because our site has to be unique. This is important!

Target Market(s)

Chinese travellers

Industry/Entity Type

Build

Requirements
Must have
• * White, blue and red
* Large spacing, not too much information cramped into a small space like sailquest.example or the current website
* More "hidden" info in popups, tabs and so on, so not to many things are visible at the same time
* Compatible with kestrel scaffold styling (for easier coding):
- http://kestrelkit.codeshelf.example/scaffold/index.html
- http://skinmarket.example/
* Feel free to propose to build the design on top of one of https://themeparlor.example/ themes if it will save the design work, will be easier and faster for you

```html
<!DOCTYPE html>
<html lang="en">
<head>
<meta charset="utf-8">
<title>Haiyun Cruises – Find Your Cruise</title>
<link href="https://fonts.googleapis.com/css2?family=Source+Sans+3:wght@400;600;700&display=swap" rel="stylesheet">
<style>
:root{
  --blue:#1f6fb2; --blue-dark:#17578f; --blue-nav:#2b80c4; --blue-side:#2d7fc0;
  --orange:#f7941d; --orange-dark:#e5780c; --text:#333; --muted:#777; --line:#e3e3e3;
  --bg-outer:#3f86c4; --foot:#4a8bc6; --foot-dark:#3b78b1; --red:#d9312b;
}
*{box-sizing:border-box;margin:0;padding:0}
html,body{width:801px;height:1200px;overflow:hidden}
body{font-family:"Source Sans 3",Arial,sans-serif;color:var(--text);
  background:radial-gradient(ellipse 60% 55% at 50% 40%,#eaf3fb 0%,#9cc4e6 45%,var(--bg-outer) 100%);position:relative}
.abs{position:absolute}
.page{position:absolute;left:120px;top:0;width:561px;height:1200px;background:#fff}
.brand{left:128px;top:22px;display:flex;align-items:center;gap:6px}
.brand-dot{width:32px;height:32px;border-radius:50%;background:var(--blue)}
.brand-name{font-size:20px;font-weight:700;color:var(--blue)}
.account{left:530px;top:12px;font-size:7px;color:var(--blue)}
.social{left:602px;top:9px;display:flex;gap:3px}
.social span{width:14px;height:14px;border-radius:3px}
.phone{left:424px;top:35px}
.phone-num{left:450px;top:32px;font-size:12px;font-weight:700;color:var(--blue)}
.phone-sub{left:450px;top:46px;font-size:9px;color:#444}
.search{left:538px;top:44px;width:132px;height:14px;border:1px solid #ccc;border-radius:2px;font-size:5.5px;color:#999;padding:3px 6px}
.nav{left:120px;top:74px;width:561px;height:23px;background:linear-gradient(#3a8fd1,var(--blue-nav));display:flex}
.nav a{font-size:6.5px;font-weight:700;color:#fff;text-decoration:none;display:flex;align-items:center;justify-content:center;border-right:1px solid rgba(255,255,255,.2)}
.nav a.on{background:var(--blue-dark)}
.finder{left:133px;top:110px;width:165px;height:234px;background:var(--blue-side);border-radius:2px;color:#fff}
.finder h2{font-size:14px;font-weight:400;padding:11px 14px 6px;border-bottom:1px solid rgba(255,255,255,.25);margin:0 4px}
.lbl{font-size:7px;color:#dce9f5}
.sel{background:#e9eef3;border-radius:2px;height:14px;font-size:5.5px;color:#333;padding:3px 6px;position:absolute}
.sel::after{content:"";position:absolute;right:0;top:0;width:10px;height:14px;border-left:1px solid #c8d0d8;background:#dfe5eb}
.go{left:13px;top:198px;width:118px;height:22px;background:linear-gradient(#fbab3c,var(--orange-dark));border-radius:2px;font-size:9.5px;font-weight:600;text-align:center;line-height:22px;color:#fff}
.news{left:133px;top:358px;width:165px;height:199px;background:var(--blue-side);border-radius:2px;color:#fff}
.photo-couple{left:8px;top:10px;width:149px;height:88px;border:3px solid #fff;background:linear-gradient(160deg,#7fc4e3,#e7c9a4 55%,#c25b3c)}
.crumb{left:316px;top:111px;font-size:6.5px;color:var(--blue)}
.panel{border:1px solid var(--line);background:#fff}
.scrollbar{width:7px;background:#f1f1f1;border-left:1px solid #ddd}
.scrollbar i{position:absolute;left:1px;width:5px;height:24px;background:#d6d6d6;border:1px solid #bbb;top:10px}
.cruise{position:absolute;width:356px;height:165px}
.cruise .pic{position:absolute;left:0;top:0;border:1px solid #ddd;padding:4px;background:#fff}
.cruise .pic div{width:100%;height:100%}
.cruise h3{position:absolute;font-size:7.5px;font-weight:600;color:var(--blue)}
.cruise .line{position:absolute;font-size:6px;color:#333}
.cruise .route{position:absolute;font-size:6px;color:#333}
.cruise .route b{font-weight:400;color:var(--blue)}
.prices{position:absolute;display:flex;gap:3px}
.prices div{width:52px;height:32px;border:1px solid #ddd;background:#f7f7f7;text-align:center;font-size:5.5px;color:#777;line-height:8px;padding-top:4px}
.prices strong{display:block;color:var(--blue);font-weight:600}
.select{position:absolute;width:40px;height:11px;background:var(--blue-dark);color:#fff;font-size:5px;font-weight:700;text-align:center;line-height:11px}
.bonus{position:absolute;left:0;font-size:7px;font-weight:600;color:var(--blue)}
.perks{position:absolute;left:0;list-style:none;font-size:5.5px;color:#444;line-height:12px}
.perks li::before{content:"»";color:var(--orange);margin-right:5px;font-weight:700}
.rule{position:absolute;left:0;height:1px;background:var(--line)}
.map{left:314px;top:482px;width:124px;height:89px;border:1px solid #ddd;padding:3px;background:#fff}
.day{left:450px;width:218px;height:24px;border:1px solid #ddd;background:linear-gradient(#fff,#eef1f4);font-size:5.5px}
.day .tag{position:absolute;left:2px;top:3px;width:34px;height:17px;background:var(--orange);border-radius:2px;color:#fff;font-weight:700;text-align:center;line-height:17px}
.day span{position:absolute;color:var(--blue)}
.day .red{color:var(--red)}
.tabs{left:313px;top:606px;display:flex;gap:2px}
.tabs div{height:21px;background:linear-gradient(#fba33a,var(--orange-dark));color:#fff;font-size:6px;font-weight:600;text-align:center;line-height:21px}
.tabs div.on{background:var(--blue-dark)}
.partners-h{left:130px;top:962px;font-size:10px;font-weight:700;color:var(--blue-dark)}
.arrow{top:963px;width:11px;height:11px;border:1px solid #ccc;background:#f2f2f2;display:flex;align-items:center;justify-content:center}
.arrow svg{display:block}
.badge{top:982px;width:83px;height:42px;border:1px solid #ddd;display:flex;align-items:center;justify-content:center;background:#fff}
.badge i{display:block;width:46px;height:14px;border-radius:3px}
.foot{left:120px;top:1038px;width:561px;height:126px;background:var(--foot);color:#fff}
.foot-bar{left:120px;top:1164px;width:561px;height:36px;background:var(--foot-dark);font-size:5.5px;color:#fff;text-align:center;line-height:32px}
.foot h4{position:absolute;font-size:8.5px;font-weight:700}
.foot ul{position:absolute;list-style:none;font-size:5.5px;line-height:12.8px}
.foot p{position:absolute;font-size:6.5px;line-height:10.5px}
.foot-logo{left:232px;top:44px;width:56px;height:54px;background:#fff;border:1px solid #cfe0ef;display:flex;flex-direction:column;align-items:center;justify-content:center;gap:3px}
.foot-logo i{width:22px;height:22px;border-radius:50%;background:var(--blue)}
.foot-logo span{font-size:5.5px;font-weight:700;color:var(--blue)}
</style>
</head>
<body>
<div class="page"></div>

<div class="abs brand"><span class="brand-dot"></span><span class="brand-name">Haiyun Cruises</span></div>
<div class="abs account">Sign in &nbsp;|&nbsp; Signup</div>
<div class="abs social"><span style="background:#e23b2e"></span><span style="background:#2aa5d8"></span><span style="background:#f08a1c"></span><span style="background:#d8332a"></span></div>
<svg class="abs phone" width="20" height="20" viewBox="0 0 20 20" aria-hidden="true"><circle cx="10" cy="10" r="9" fill="none" stroke="#888" stroke-width="1.2"/><path d="M7 5l2 2-1 2c1 2 2 3 4 4l2-1 2 2-2 2C9 16 4 11 5 6z" fill="#888"/></svg>
<div class="abs phone-num">400 880 218</div>
<div class="abs phone-sub">Call Us Today!</div>
<div class="abs search">SEARCH :</div>

<nav class="abs nav">
  <a class="on" style="width:62px">HOME</a><a style="width:74px">DESTINATIONS</a><a style="width:74px">CRUISE LINES</a><a style="width:74px">CRUISE INFO</a><a style="width:54px">DEALS</a><a style="width:84px">ONLINE BOOKING</a><a style="width:82px">CONTACT US</a><a style="width:57px;border:0">BLOG</a>
</nav>

<section class="abs finder">
  <h2>Find Your Cruise</h2>
  <div class="abs lbl" style="left:13px;top:39px">Destination</div>
  <div class="sel" style="left:13px;top:50px;width:137px">Destination name</div>
  <div class="abs lbl" style="left:13px;top:70px">Length</div>
  <div class="abs lbl" style="left:88px;top:70px">Month</div>
  <div class="sel" style="left:13px;top:80px;width:62px">Length Area</div>
  <div class="sel" style="left:88px;top:80px;width:62px"></div>
  <div class="abs lbl" style="left:12px;top:102px">Cruise Lines</div>
  <div class="sel" style="left:12px;top:113px;width:138px">Any Cruise line</div>
  <div class="abs" style="left:12px;top:136px;font-size:8px">Number of Travelers</div>
  <div class="abs lbl" style="left:13px;top:151px">Age 25+</div>
  <div class="abs lbl" style="left:88px;top:151px">Age 0 to 24</div>
  <div class="sel" style="left:13px;top:163px;width:62px">5</div>
  <div class="sel" style="left:88px;top:163px;width:62px">0</div>
  <div class="abs" style="left:13px;top:183px;font-size:5.5px;color:#dce9f5;display:flex;gap:3px;align-items:center"><span style="width:7px;height:7px;background:#e9eef3;display:inline-block"></span>Check for senior rates</div>
  <div class="abs go">Search Cruises</div>
</section>

<section class="abs news">
  <div class="abs photo-couple" role="img" aria-label="Retired couple relaxing by a pool with flower garlands"></div>
  <div class="abs" style="left:13px;top:106px;font-size:8px;font-weight:700">Cruise Deals Newsletter</div>
  <div class="abs" style="left:13px;top:120px;font-size:5.5px">Subscribe to the best Cruise deals Now!</div>
  <div class="abs" style="left:13px;top:137px;width:143px;height:14px;background:#fff;border-radius:2px;font-size:5.5px;color:#999;padding:3px 6px">Email :</div>
  <div class="abs" style="left:13px;top:160px;width:58px;height:15px;background:#17497a;font-size:6px;text-align:center;line-height:15px">Subscribe</div>
  <div class="abs" style="left:13px;top:180px;font-size:6.5px">Contest Rules</div>
</section>

<div class="abs crumb">HOME &nbsp;›&nbsp; ABOUT US</div>

<div class="abs" style="left:312px;top:132px;width:365px;height:336px;overflow:hidden">
  <div class="cruise" style="left:0;top:0">
    <div class="pic" style="width:124px;height:90px"><div role="img" aria-label="Cruise ship at sea under a sunset sky" style="background:linear-gradient(#7a90b8,#d9a48c 40%,#3d6fa3 60%,#1e4f80)"></div></div>
    <h3 style="left:134px;top:1px">3 DAYS BAHAMAS</h3>
    <div class="line" style="left:134px;top:15px">NORDVALE CRUISE LINE. NORDVALE SKYE</div>
    <div class="route" style="left:134px;top:28px"><b>Miami, Great ay, Nassau, Miami</b> &nbsp;| &nbsp; 4 departure dates : Sep 6, 13, 20, 27 2013</div>
    <div class="prices" style="left:134px;top:44px"><div>Inside from<strong>$174</strong>$58 per day</div><div>Ocean view from<strong>$174</strong>$58 per day</div><div>Inside from<strong>$174</strong>$58 per day</div><div>Inside from<strong>$174</strong>$58 per day</div></div>
    <div class="select" style="left:314px;top:90px">SELECT</div>
    <div class="bonus" style="top:101px">BONUS OFFER</div>
    <ul class="perks" style="top:115px"><li>EXCLUSIVE Free Prepaid Gratuities</li><li>Free Upgrades when you sail to the Bahamas, Bermuda or Caribbean</li><li>Enjoy a 1 Night Pre or Post Cruise Discounted Miami Hotel Add-On</li></ul>
    <div class="rule" style="top:162px;width:356px"></div>
  </div>
  <div class="cruise" style="left:0;top:175px">
    <div class="pic" style="width:124px;height:90px"><div role="img" aria-label="White cruise ship on calm blue water" style="background:linear-gradient(#cfe2f2,#7fb0d8 55%,#2b6aa3)"></div></div>
    <h3 style="left:134px;top:1px">3 DAYS BAHAMAS</h3>
    <div class="line" style="left:134px;top:15px">NORDVALE CRUISE LINE. NORDVALE SKYE</div>
    <div class="route" style="left:134px;top:28px"><b>Miami, Great ay, Nassau, Miami</b> &nbsp;| &nbsp; 4 departure dates : Sep 6, 13, 20, 27 2013</div>
    <div class="prices" style="left:134px;top:44px"><div>Inside from<strong>$174</strong>$58 per day</div><div>Ocean view from<strong>$174</strong>$58 per day</div><div>Inside from<strong>$174</strong>$58 per day</div><div>Inside from<strong>$174</strong>$58 per day</div></div>
    <div class="select" style="left:314px;top:90px">SELECT</div>
    <div class="bonus" style="top:101px">BONUS OFFER</div>
    <ul class="perks" style="top:115px"><li>EXCLUSIVE Free Prepaid Gratuities</li><li>Free Upgrades when you sail to the Bahamas, Bermuda or Caribbean</li><li>Enjoy a 1 Night Pre or Post Cruise Discounted Miami Hotel Add-On</li></ul>
  </div>
  <div class="abs scrollbar" style="left:357px;top:0;height:336px"><i></i></div>
</div>

<div class="abs map"><div role="img" aria-label="Itinerary map of the cruise route" style="width:100%;height:100%;background:linear-gradient(#e4eae2,#d9e3e0)"></div></div>

<div class="abs day" style="top:482px"><div class="tag">DAY-1</div><span style="left:40px;top:4px">THU</span><span style="left:65px;top:4px">SEP 5</span><span style="left:94px;top:4px">PORT CANAVERAL</span><span class="red" style="left:94px;top:14px">ARRIVE : 3:45PM</span><span class="red" style="left:168px;top:14px">DEPART 3:45PM</span></div>
<div class="abs day" style="top:511px"><div class="tag">DAY-1</div><span style="left:40px;top:4px">THU</span><span style="left:65px;top:4px">SEP 5</span><span style="left:94px;top:4px">PORT CANAVERAL</span><span class="red" style="left:94px;top:14px">ARRIVE : 3:45PM</span><span class="red" style="left:168px;top:14px">DEPART 3:45PM</span></div>
<div class="abs day" style="top:539px"><div class="tag">DAY-1</div><span style="left:40px;top:4px">THU</span><span style="left:65px;top:4px">SEP 5</span><span style="left:94px;top:4px">PORT CANAVERAL</span><span class="red" style="left:94px;top:14px">ARRIVE : 3:45PM</span><span class="red" style="left:168px;top:14px">DEPART 3:45PM</span></div>
<div class="abs day" style="top:568px"><div class="tag">DAY-1</div><span style="left:40px;top:4px">THU</span><span style="left:65px;top:4px">SEP 5</span><span style="left:94px;top:4px">PORT CANAVERAL</span><span class="red" style="left:94px;top:14px">ARRIVE : 3:45PM</span><span class="red" style="left:168px;top:14px">DEPART 3:45PM</span></div>

<div class="abs tabs"><div class="on" style="width:82px">SAILING</div><div style="width:77px">SHIP</div><div style="width:76px">DECKS</div><div style="width:76px">HIGHLIGHTS</div></div>

<div class="abs panel" style="left:313px;top:627px;width:364px;height:321px;overflow:hidden">
  <div class="cruise" style="left:8px;top:12px">
    <div class="pic" style="width:104px;height:82px"><div role="img" aria-label="Illuminated cruise ship docked at dusk" style="background:linear-gradient(#1f3d66,#3d6aa0 45%,#c98a4a 70%,#2b3f5a)"></div></div>
    <h3 style="left:112px;top:2px">3 DAYS BAHAMAS</h3>
    <div class="line" style="left:112px;top:16px">NORDVALE CRUISE LINE. NORDVALE SKYE</div>
    <div class="route" style="left:112px;top:29px"><b>Miami, Great ay, Nassau, Miami</b> &nbsp;| &nbsp; 4 departure dates : Sep 6, 13, 20, 27 2013</div>
    <div class="prices" style="left:112px;top:45px"><div>Inside from<strong>$174</strong>$58 per day</div><div>Ocean view from<strong>$174</strong>$58 per day</div><div>Inside from<strong>$174</strong>$58 per day</div><div>Inside from<strong>$174</strong>$58 per day</div></div>
    <div class="select" style="left:292px;top:89px">SELECT</div>
    <div class="bonus" style="top:101px">BONUS OFFER</div>
    <ul class="perks" style="top:115px"><li>EXCLUSIVE Free Prepaid Gratuities</li><li>Free Upgrades when you sail to the Bahamas, Bermuda or Caribbean</li></ul>
    <div class="rule" style="top:146px;width:330px"></div>
  </div>
  <div class="cruise" style="left:8px;top:170px">
    <div class="pic" style="width:104px;height:82px"><div role="img" aria-label="Cruise ship sailing on deep blue sea" style="background:linear-gradient(#e9b98a,#9fc0de 40%,#2f74b6 65%,#1b4f86)"></div></div>
    <h3 style="left:112px;top:2px">3 DAYS BAHAMAS</h3>
    <div class="line" style="left:112px;top:16px">NORDVALE CRUISE LINE. NORDVALE SKYE</div>
    <div class="route" style="left:112px;top:29px"><b>Miami, Great ay, Nassau, Miami</b> &nbsp;| &nbsp; 4 departure dates : Sep 6, 13, 20, 27 2013</div>
    <div class="prices" style="left:112px;top:45px"><div>Inside from<strong>$174</strong>$58 per day</div><div>Ocean view from<strong>$174</strong>$58 per day</div><div>Inside from<strong>$174</strong>$58 per day</div><div>Inside from<strong>$174</strong>$58 per day</div></div>
    <div class="select" style="left:292px;top:89px">SELECT</div>
    <div class="bonus" style="top:101px">BONUS OFFER</div>
    <ul class="perks" style="top:115px"><li>EXCLUSIVE Free Prepaid Gratuities</li><li>Free Upgrades when you sail to the Bahamas, Bermuda or Caribbean</li></ul>
  </div>
  <div class="abs scrollbar" style="left:355px;top:0;height:321px"><i></i></div>
</div>

<div class="abs partners-h">OUR RELIABLE PARTNERS</div>
<div class="abs arrow" style="left:645px"><svg width="7" height="7" viewBox="0 0 9 9"><path d="M5.5 2L3 4.5 5.5 7" fill="none" stroke="#888"/></svg></div>
<div class="abs arrow" style="left:659px"><svg width="7" height="7" viewBox="0 0 9 9"><path d="M3.5 2L6 4.5 3.5 7" fill="none" stroke="#888"/></svg></div>
<div class="abs badge" style="left:131px"><i style="background:#c9c9c9"></i></div>
<div class="abs badge" style="left:223px"><i style="background:#c9d7ea"></i></div>
<div class="abs badge" style="left:314px"><i style="background:#d3d9e1"></i></div>
<div class="abs badge" style="left:406px"><i style="background:#f6d2a6"></i></div>
<div class="abs badge" style="left:497px"><i style="background:#cfe3f3"></i></div>
<div class="abs badge" style="left:589px"><i style="background:#c5dcf0"></i></div>

<footer class="abs foot">
  <h4 style="left:18px;top:21px">Useful Pages</h4>
  <ul style="left:18px;top:37px"><li>About Us</li><li>Contact us</li><li>Blog</li><li>FAQ</li><li>Terms of Service</li><li>Payment info</li><li>Reward Points</li></ul>
  <h4 style="left:127px;top:21px">Cruise Infov</h4>
  <ul style="left:128px;top:37px"><li>Cruise news</li><li>Visa</li><li>Honeymoon cruises</li><li>Firsttime on a Cruise</li></ul>
  <h4 style="left:232px;top:25px;font-size:8px">About haiyuncruise.example</h4>
  <div class="abs foot-logo"><i></i><span>Haiyun</span></div>
  <p style="left:300px;top:46px;width:70px">We're the most advanced cruise booking providr in china.</p>
  <h4 style="left:404px;top:25px;font-size:8px">Contact Us</h4>
  <p style="left:404px;top:42px;width:150px">Harbourline Studio Pte Ltd<br>Lotus Centre x118, Bay Ave 7.2<br>Riverton 20517</p>
  <svg class="abs" style="left:404px;top:81px" width="9" height="8" viewBox="0 0 9 8" aria-hidden="true"><path d="M1 3C1 1 8 1 8 3L7 4 6 3H3L2 4z M2 4h5v3H2z" fill="#fff"/></svg>
  <p style="left:416px;top:79px">(555) 010-2468 - (555) 010-1357</p>
  <svg class="abs" style="left:404px;top:95px" width="9" height="7" viewBox="0 0 9 7" aria-hidden="true"><rect x=".5" y=".5" width="8" height="6" fill="#fff"/><path d="M.5 .5l4 3.5 4-3.5" fill="none" stroke="#4a8bc6"/></svg>
  <p style="left:416px;top:93px">hello@haiyuncruise.example</p>
</footer>
<div class="abs foot-bar">© 2013. haiyuncruise.example. All rights reserved.</div>
</body>
</html>
```